Maple Roster Business Card for recruitment company

We are looking for a Business Card Design that incorporates our personal details and our busines name and logo. We are a specialized search consultancy that recruit Property and Construction professionals.
We would like a business card that stands out and is appealing to the Construction and Property industry as well.

Target Market(s)

people in the construction and property industry

Contact Information for Business Card

Business Name and logo

Font styles to use
Serif

Colors
0094D4
00A9DD
6FCCEA
C7EBF8
E9F6FB

Requirements
Must have
• Business name and logo as well as contact details
Should not have
• No photos of us please

```html
<!DOCTYPE html>
<html lang="en">
<head>
<meta charset="UTF-8">
<title>Maple Roster – Business Card</title>
<link href="https://fonts.googleapis.com/css2?family=Poppins:wght@300;400;600&display=swap" rel="stylesheet">
<style>
  :root {
    --teal: #033f54;
    --orange: #f07a22;
    --white: #ffffff;
    --ink: #0b3a4d;
    --stage: #e6e8ea;
  }
  * { margin: 0; padding: 0; box-sizing: border-box; }
  html, body { width: 1200px; height: 780px; overflow: hidden; }
  body {
    background: var(--stage);
    font-family: "Poppins", sans-serif;
    position: relative;
  }
  .card {
    position: absolute;
    width: 540px;
    height: 310px;
    border-radius: 16px;
    overflow: hidden;
    background: var(--teal);
    box-shadow: 0 10px 30px rgba(0,0,0,0.18);
  }
  .card--front { left: 620px; top: 235px; }
  .card--back  { left: 40px;  top: 235px; }

  /* Front */
  .front-name {
    position: absolute;
    left: 0; right: 0; top: 105px;
    text-align: center;
    color: var(--white);
    font-weight: 300;
    font-size: 46px;
    letter-spacing: 4px;
    text-transform: uppercase;
  }
  .front-band {
    position: absolute;
    left: 0; right: 0; bottom: 0;
    height: 44px;
    background: var(--orange);
    display: flex;
    align-items: center;
    padding-left: 60px;
    gap: 10px;
    color: var(--white);
    font-size: 15px;
    font-weight: 600;
    letter-spacing: 1.5px;
  }
  .front-band svg { width: 18px; height: 18px; }

  /* Back */
  .back-circle {
    position: absolute;
    left: 180px; top: 95px;
    width: 560px; height: 560px;
    border-radius: 50%;
    background: var(--white);
  }
  .back-name-logo {
    position: absolute;
    left: 235px; top: 185px;
    width: 280px;
    text-align: center;
    color: var(--ink);
    font-weight: 300;
    font-size: 30px;
    letter-spacing: 3px;
    text-transform: uppercase;
  }
  .contact {
    position: absolute;
    left: 28px; top: 26px;
    color: var(--white);
  }
  .contact__name { font-size: 19px; font-weight: 600; letter-spacing: 1px; line-height: 1.1; }
  .contact__role { font-size: 11px; color: var(--orange); letter-spacing: 1px; margin-bottom: 14px; }
  .contact__address { font-size: 13px; line-height: 1.35; letter-spacing: 0.8px; margin-bottom: 12px; }
  .contact__list { list-style: none; font-size: 11.5px; letter-spacing: 0.6px; }
  .contact__list li { display: flex; align-items: center; gap: 8px; line-height: 1.75; }
  .contact__list svg { width: 12px; height: 12px; flex: none; }
</style>
</head>
<body>

  <section class="card card--back" aria-label="Business card back">
    <div class="back-circle"></div>
    <div class="back-name-logo">Maple Roster</div>
    <div class="contact">
      <p class="contact__name">Idris Kamal</p>
      <p class="contact__role">General Manager</p>
      <p class="contact__address">4820 Harbor Row<br>Lane Fenwick,<br>VA 20400</p>
      <ul class="contact__list">
        <li>
          <svg viewBox="0 0 24 24"><path fill="#f07a22" d="M6.6 10.8a15 15 0 0 0 6.6 6.6l2.2-2.2a1 1 0 0 1 1-.25 11.4 11.4 0 0 0 3.6.6 1 1 0 0 1 1 1V20a1 1 0 0 1-1 1A17 17 0 0 1 3 4a1 1 0 0 1 1-1h3.5a1 1 0 0 1 1 1c0 1.25.2 2.45.6 3.6a1 1 0 0 1-.25 1z"/></svg>
          041-552-7730
        </li>
        <li>
          <svg viewBox="0 0 24 24"><path fill="#f07a22" d="M6.6 10.8a15 15 0 0 0 6.6 6.6l2.2-2.2a1 1 0 0 1 1-.25 11.4 11.4 0 0 0 3.6.6 1 1 0 0 1 1 1V20a1 1 0 0 1-1 1A17 17 0 0 1 3 4a1 1 0 0 1 1-1h3.5a1 1 0 0 1 1 1c0 1.25.2 2.45.6 3.6a1 1 0 0 1-.25 1z"/></svg>
          041-552-7730
        </li>
        <li>
          <svg viewBox="0 0 24 24"><rect x="2" y="5" width="20" height="14" fill="#f07a22"/><path d="M2 5l10 8 10-8" stroke="#033f54" stroke-width="1.6" fill="none"/></svg>
          idris@mapleroster.com
        </li>
        <li>
          <svg viewBox="0 0 24 24"><g fill="none" stroke="#f07a22" stroke-width="2"><circle cx="12" cy="12" r="9"/><ellipse cx="12" cy="12" rx="4" ry="9"/><path d="M3 12h18"/></g></svg>
          www.mapleroster.com
        </li>
      </ul>
    </div>
  </section>

  <section class="card card--front" aria-label="Business card front">
    <div class="front-name">Maple Roster</div>
    <div class="front-band">
      <svg viewBox="0 0 24 24"><g fill="none" stroke="#ffffff" stroke-width="2"><circle cx="12" cy="12" r="9"/><ellipse cx="12" cy="12" rx="4" ry="9"/><path d="M3 12h18"/></g></svg>
      www.mapleroster.com
    </div>
  </section>

</body>
</html>
```